Business Card Design Project

I need a business card designed from scratch. I have an existing logo that I can upload in Illustrator for modification or redesign.

The Company is called Query Lanterns http://querylanterns.com.au and we provide Search Engine Optimization services to Australian businesses. The current logo signifies an increase in visitors, profits etc...

There are no restrictions as to the redesign - colours, style etc are all open to change.

Cards will be full colour and one sided printed at http://www.cardmoxel.com.au so check their requirements for file format and sizes etc.

I will expect all original files upon completion of project.

Target Market(s)

Any business with a web site looking to improve their search engine rankings

Industry/Entity Type

Business

Requirements
Must have
• I like modern, sleek designs. Clean, not fussy, uncluttered.

```html
<!DOCTYPE html>
<html lang="en">
<head>
<meta charset="utf-8">
<title>Query Lanterns – Business Cards</title>
<link rel="stylesheet" href="https://fonts.googleapis.com/css2?family=Open+Sans:wght@400;600;700;800&display=swap">
<style>
  :root {
    --backdrop: #e9e6e2;
    --card-white: #ffffff;
    --band-black: #000000;
    --brand-yellow: #f5c400;
    --brand-blue: #1f6fb8;
    --contact-blue: #3a8fd6;
    --ink-grey: #4a4a4a;
  }
  * { box-sizing: border-box; margin: 0; padding: 0; }
  html, body { width: 1200px; height: 460px; overflow: hidden; }
  body {
    background: var(--backdrop);
    font-family: "Open Sans", Arial, sans-serif;
    position: relative;
  }
  .card {
    position: absolute;
    background: var(--card-white);
    box-shadow: 0 2px 8px rgba(0,0,0,0.25);
    overflow: hidden;
  }
  .card--front { left: 52px; top: 46px; width: 542px; height: 338px; }
  .card--back  { left: 606px; top: 74px; width: 542px; height: 303px; }

  .contact-band {
    position: absolute; left: 0; top: 0; width: 100%; height: 156px;
    background: var(--band-black);
  }
  .contact-band::after {
    content: ""; position: absolute; left: 0; right: 0; bottom: -8px;
    height: 4px; background: var(--brand-yellow);
  }
  .person {
    position: absolute; top: 50px; left: 0; width: 100%;
    text-align: center; color: var(--brand-yellow);
  }
  .person__name { font-weight: 700; font-size: 17px; }
  .person__title { font-weight: 400; font-size: 13px; }

  .contact-grid {
    position: absolute; left: 26px; top: 93px;
    display: grid; grid-template-columns: 168px 104px auto;
    row-gap: 4px; column-gap: 10px;
    color: var(--contact-blue); font-size: 12.5px; line-height: 16px;
  }
  .contact-item { display: flex; align-items: center; gap: 5px; white-space: nowrap; }
  .contact-item svg { width: 10px; height: 10px; fill: var(--contact-blue); flex: none; }

  .wordmark {
    position: absolute; display: flex; align-items: center; gap: 12px;
    color: var(--brand-blue); font-weight: 800; white-space: nowrap;
  }
  .wordmark__dot {
    width: 18px; height: 18px; border-radius: 50%; background: var(--brand-yellow);
  }
  .card--front .wordmark { left: 0; right: 0; justify-content: center; top: 240px; font-size: 34px; }
  .card--back .wordmark  { left: 0; right: 0; justify-content: center; top: 135px; font-size: 36px; }

  .web-address {
    position: absolute; left: 0; right: 0; top: 210px; text-align: center;
    color: var(--ink-grey); font-size: 13px; letter-spacing: 2.4px;
  }
</style>
</head>
<body>

<section class="card card--front" aria-label="Business card front">
  <div class="contact-band">
    <p class="person"><span class="person__name">Your Name</span> <span class="person__title">Title</span></p>
    <div class="contact-grid">
      <span class="contact-item">00Floor Street, City Name</span>
      <span class="contact-item"><svg viewBox="0 0 10 10"><path d="M2 0.5 L3.8 2.5 L3 3.7 Q4.3 6 6.3 7 L7.5 6.2 L9.5 8 L8.3 9.6 Q2.5 8.5 0.5 1.7Z"/></svg>098 765 4321</span>
      <span class="contact-item"><svg viewBox="0 0 10 10"><path d="M0.5 2 H9.5 V8 H0.5Z M1 2.3 L5 5.5 L9 2.3" fill="none" stroke="#3a8fd6" stroke-width="1.2"/></svg>enquiry@querylanterns.com.au</span>
      <span class="contact-item">State Name, Contry Name</span>
      <span class="contact-item"><svg viewBox="0 0 10 10"><rect x="2.5" y="0.5" width="5" height="9" rx="1"/><rect x="3.4" y="1.6" width="3.2" height="5" fill="#000"/></svg>098 765 4321</span>
      <span class="contact-item"><svg viewBox="0 0 10 10"><circle cx="5" cy="5" r="4.5"/></svg>www.querylanterns.com.au</span>
    </div>
  </div>
  <div class="wordmark"><span class="wordmark__dot"></span>Query Lanterns</div>
</section>

<section class="card card--back" aria-label="Business card back">
  <div class="wordmark"><span class="wordmark__dot"></span>Query Lanterns</div>
  <p class="web-address">www.querylanterns.com.au</p>
</section>

</body>
</html>
```